Maple Lantern Productions web site

I need to build a website for a new company I am launching next month. Maple Lantern Productions is a company based in New England that provides sound, lighting, and audio visual services to weddings, corporate, and any other cusomer base looking for quality service for a fair price. Looking for somebody to do a full site not just the image files. I am looking to keep the colors of my logo (orange and black) and possibly grey and white. I am looking to build my site very similar to brightvaleevents.example, which is owned by a friend of mine. I like how he has the big pictures that load in to the site and the basic menu items. I'll need a gallery of photos. The designs should communicate quality, value and trust.
My website address is maplelanternco.example.
Updates

Hi and thanks to everyone for posting such great ideas for our new design.I have some items that I'd like to ask you all to focus on in your revisions.I like how http://www.brightvaleevents.example/ website has five or six high res pictures that change in a slideshow format with a caption that loads in for each one for the different types of services. Try and capture pics like these and with teh same headings as he has. The basic menu designs have been interesting.I am more fond of the menus that are more white with some orange as I dont want it to be too dark. I'm curious to see how your galleries will work and if i'll be able to edit the pages myself? I have some more info on the company for you to fill in:website address is ciderhouseco.comemail: info@ciderhouseco.comaddress: Maple Lantern Productions57 Littlefield StreetAvon, MA 02417"New England's finest DJ's, lighting and sound, video and more. Creating memories one perfect event at a time."Put this under the loading pictures as a tagline.About Cider HouseCider House Productions is a collection of New England's finest talent, ready to make your next event the one you've dreamed of. We have the skills and expertise to deliver your vision of your perfect event. From elegant weddings to themed mitzvah's, corporate av, videography and detail lighting, we offer all of the elements to make your event a success. Added Wednesday, March 1, 2017

Designer's Please also make sure that your design flows well on any device it is being viewed on as well. Thanks. Added Wednesday, March 1, 2017

Project Deadline Extended Reason: Hello designerThank you all very much for your hard work on our project. Im sorry but i need to extend the date of my project. Our parent conpany Rook Nine Prodactions sponsors Bay Youth Assemblies and we are currently at their leadership conference on the Cape. I will be back in on Monday and with your help will get this finished by Thursday the 16th. Thanks Added Thursday, March 9, 2017

Project Deadline Extended Reason: One of the designers is not responding so I now have to make revisions with other designers. I hope to get this website done over the weekends so please get your revisions as soon as possible. Thank you. I am also upgrading the budget another $75 to hopefully get some more interest on my project. Added Wednesday, March 15, 2017

Target Market(s)

Wedding - Corporate -

Industry/Entity Type

It Company

Coding

Coded - Design and coding required

Number of Pages Required

5+ page

Font styles to use
Sans Serif

Requirements
Must have
• Photo Gallery - I want to be able to edit it myself
Nice to have
• I like the look of my friends website brightvaleevents.example

```html
<!DOCTYPE html>
<html lang="en">
<head>
<meta charset="utf-8">
<title>Maple Lantern Productions</title>
<link href="https://fonts.googleapis.com/css2?family=Questrial&display=swap" rel="stylesheet">
<style>
  :root {
    --orange: #f26a2e;
    --ink: #2b2b2b;
    --muted: #6d6d6d;
    --line: #cfcfcf;
    --white: #ffffff;
    --canvas: #ececec;
    --grey-btn: #bdbdbd;
    --dark: #1c1613;
  }
  * { box-sizing: border-box; margin: 0; padding: 0; }
  html, body { width: 890px; height: 1200px; overflow: hidden; background: var(--canvas); }
  body { font-family: "Questrial", sans-serif; position: relative; }

  .page {
    position: absolute; left: 259px; top: 2px;
    width: 372px; height: 1308px;
    transform: scale(0.914); transform-origin: top center;
    background: var(--white); overflow: hidden;
  }

  /* Hero */
  .hero { position: absolute; left: 0; top: 0; width: 372px; height: 265px; }
  .hero-photo {
    position: absolute; inset: 0;
    background:
      linear-gradient(180deg, rgba(255,255,255,0) 55%, rgba(246,236,238,.92) 66%, rgba(244,234,236,.95) 96%, #e7c9cc 100%),
      radial-gradient(ellipse at 50% 35%, #c9b6c8 0%, #7a5a78 45%, #3b2a3e 100%);
  }
  .site-header {
    position: absolute; left: 9px; top: 8px; width: 353px; height: 38px;
    background: rgba(255,255,255,.82);
    display: flex; align-items: center; padding: 0 14px 0 13px;
  }
  .brand { display: flex; align-items: center; gap: 6px; }
  .brand-dot { width: 22px; height: 22px; border-radius: 50%; background: var(--orange); }
  .brand-name { font-size: 10px; color: var(--ink); letter-spacing: .2px; }
  .menu-toggle { margin-left: auto; width: 11px; display: flex; flex-direction: column; gap: 2px; }
  .menu-toggle span { height: 2px; background: var(--ink); }

  .availability { position: absolute; left: 47px; top: 187px; width: 281px; }
  .field {
    position: absolute; width: 133px; height: 22px; background: var(--white);
    border: 1px solid #ece4e6; font-size: 8px; color: #a6a6a6;
    display: flex; align-items: center; justify-content: space-between; padding: 0 6px;
  }
  .field svg { width: 7px; height: 5px; }
  .btn-check {
    position: absolute; left: 148px; top: 32px; width: 133px; height: 22px;
    background: var(--orange); color: var(--white); font-size: 8.5px;
    display: flex; align-items: center; justify-content: center; border-radius: 2px;
  }

  /* Intro */
  .intro { position: absolute; left: 0; top: 265px; width: 372px; height: 233px; text-align: center; }
  .intro h1 { font-weight: 400; font-size: 17px; color: var(--ink); margin-top: 15px; }
  .divider { position: relative; height: 10px; margin: 8px auto 0; }
  .divider::before { content: ""; position: absolute; left: 0; right: 0; top: 4px; border-top: 1px solid var(--line); }
  .divider svg { position: absolute; left: 50%; top: 0; margin-left: -5px; width: 10px; height: 7px; }
  .intro .divider { width: 278px; }
  .intro p { font-size: 10px; line-height: 15.5px; color: var(--muted); width: 344px; margin: 13px auto 0; }
  .btn-help {
    display: flex; align-items: center; justify-content: center;
    width: 188px; height: 34px; margin: 16px auto 0;
    background: var(--grey-btn); color: #555; font-size: 12px;
  }

  /* Services */
  .services { position: absolute; left: 0; top: 498px; width: 372px; height: 810px; text-align: center; }
  .services-photo {
    position: absolute; inset: 0;
    background:
      radial-gradient(ellipse at 85% 45%, rgba(150,70,50,.55) 0%, rgba(40,25,20,0) 45%),
      radial-gradient(ellipse at 20% 30%, rgba(90,60,40,.5) 0%, rgba(0,0,0,0) 50%),
      linear-gradient(180deg, #2c2420 0%, #1f1814 50%, #17110f 100%);
  }
  .services-inner { position: relative; }
  .services h2 { font-weight: 400; font-size: 16px; color: var(--white); padding-top: 30px; }
  .services .divider { width: 299px; margin-top: 6px; }
  .services .divider::before { border-color: rgba(255,255,255,.25); }
  .service-list { margin-top: 27px; }
  .service { height: 177px; }
  .service-icon {
    width: 50px; height: 50px; margin: 0 auto; border-radius: 50%;
    border: 1px solid rgba(255,255,255,.85);
    display: flex; align-items: center; justify-content: center;
  }
  .service-icon svg { width: 20px; height: 20px; }
  .service h3 { font-weight: 400; font-size: 14px; color: var(--white); margin-top: 12px; }
  .service p { font-size: 9.5px; line-height: 14px; color: #e6e6e6; width: 190px; margin: 8px auto 0; }
  .service a { display: block; font-size: 11px; color: var(--orange); text-decoration: none; margin-top: 8px; }
</style>
</head>
<body>
<main class="page">
  <section class="hero">
    <div class="hero-photo" role="img" aria-label="Photo of a bride and groom dancing at a reception with guests and stage lights"></div>
    <header class="site-header">
      <div class="brand"><span class="brand-dot"></span><span class="brand-name">MAPLE LANTERN PRODUCTIONS</span></div>
      <div class="menu-toggle"><span></span><span></span><span></span></div>
    </header>
    <form class="availability">
      <div class="field" style="left:0;top:0">Month<svg viewBox="0 0 7 5"><path d="M1 1l2.5 2.5L6 1" stroke="#777" fill="none"/></svg></div>
      <div class="field" style="left:148px;top:0">Day<svg viewBox="0 0 7 5"><path d="M1 1l2.5 2.5L6 1" stroke="#777" fill="none"/></svg></div>
      <div class="field" style="left:0;top:32px">Year<svg viewBox="0 0 7 5"><path d="M1 1l2.5 2.5L6 1" stroke="#777" fill="none"/></svg></div>
      <div class="btn-check">Check Availability</div>
    </form>
  </section>

  <section class="intro">
    <h1>Maple Lantern are Experts in All Type of Events</h1>
    <div class="divider"><svg viewBox="0 0 10 7"><path d="M1 1l4 4 4-4" stroke="#bbb" fill="#fff"/></svg></div>
    <p>Lorem Ipsum is simply dummy text of the printing and typesetting industry. Lorem Ipsum has been the industry's standard dummy text ever since the 1500s, when an unknown printer took a galley of type and scrambled it to make a type specimen book. It has survived not only five centuries, but also the leap into electronic typesetting, remaining essentially unchanged. It was popularised in the</p>
    <div class="btn-help">How can we help you ?</div>
  </section>

  <section class="services">
    <div class="services-photo" role="img" aria-label="Dim photo of a hand holding a glass of red wine at an evening event"></div>
    <div class="services-inner">
      <h2>Our Services</h2>
      <div class="divider"><svg viewBox="0 0 10 7"><path d="M1 1l4 4 4-4" stroke="#aaa" fill="#231c18"/></svg></div>
      <div class="service-list">
        <article class="service">
          <div class="service-icon"><svg viewBox="0 0 20 20"><rect x="3" y="6" width="14" height="10" rx="1" fill="#fff"/><rect x="7.5" y="3.5" width="5" height="3" fill="none" stroke="#fff" stroke-width="1.4"/></svg></div>
          <h3>Corporate Events</h3>
          <p>Lorem Ipsum is simply dummy text of the printing and typesetting industry. Lorem Ipsum has been the industry's</p>
          <a href="#">See Our Packages</a>
        </article>
        <article class="service">
          <div class="service-icon"><svg viewBox="0 0 20 20"><circle cx="7" cy="13" r="3.5" fill="#fff"/><path d="M8 12L15 4" stroke="#fff" stroke-width="1.8"/><path d="M14 3l3 2" stroke="#fff" stroke-width="1.6"/></svg></div>
          <h3>Music Concert</h3>
          <p>Lorem Ipsum is simply dummy text of the printing and typesetting industry. Lorem Ipsum has been the industry's</p>
          <a href="#">See Our Packages</a>
        </article>
        <article class="service">
          <div class="service-icon"><svg viewBox="0 0 20 20"><circle cx="7.5" cy="12" r="4.5" fill="none" stroke="#fff" stroke-width="1.6"/><circle cx="12.5" cy="12" r="4.5" fill="none" stroke="#fff" stroke-width="1.6"/><path d="M6 5l1.5-2 1.5 2-1.5 1.5z" fill="#fff"/></svg></div>
          <h3>Wedding Plane</h3>
          <p>Lorem Ipsum is simply dummy text of the printing and typesetting industry. Lorem Ipsum has been the industry's</p>
          <a href="#">See Our Packages</a>
        </article>
        <article class="service">
          <div class="service-icon"><svg viewBox="0 0 20 20"><path d="M1 8l9-4 9 4-9 4z" fill="#fff"/><path d="M5 10v4c2 2 8 2 10 0v-4l-5 2z" fill="#fff"/><path d="M3 9v6" stroke="#fff" stroke-width="1"/></svg></div>
          <h3>School and Formal Events</h3>
          <p>Lorem Ipsum is simply dummy text of the printing and typesetting industry. Lorem Ipsum has been the industry's</p>
          <a href="#">See Our Packages</a>
        </article>
      </div>
    </div>
  </section>
</main>
</body>
</html>
```